New Business Card Design Project

We require a business card design for Vexalund, a newly established Indian company.
Our focus is on the development, manufacturing, and export of a diverse array of pharmaceutical products on a global scale. The card should convey a professional appearance, as our primary markets are in Africa, China, and Southeast Asian nations.
We envision a two-sided business card, with the reverse side dedicated to a logo set against a solid color or an elegantly designed pattern. The corners should be rounded. We would appreciate seeing both horizontal and vertical design options. We trust the designer to utilize their expertise in creating this design.

The content for the business card is included in the attached Word file.

Target Market(s)

Our primary markets are in Africa, China, and Southeast Asian, Latin America, Maldives, Sri Lanka

Industry/Entity Type

Pharmaceutical Manufacturing and Export

Contact Information for Business Card

Colors

Designer to choose colors to be used in the design.

Requirements
Must have
• The reverse side of the business card features solely the logo along with the tagline, "Cures Across Borders."
Should not have
• The logo should not exceed two instances, encompassing both the front and back sides of the card.

```html
<!DOCTYPE html>
<html lang="en">
<head>
<meta charset="utf-8">
<title>Vexalund Business Card</title>
<link rel="stylesheet" href="https://fonts.googleapis.com/css2?family=Cabin:wght@400;600;700&family=Alegreya+Sans:wght@500&display=swap">
<style>
  :root {
    --backdrop: #2e2e30;
    --coral: #e45a47;
    --coral-light: #ef6450;
    --brand-blue: #2391c9;
    --ink: #3a3a3a;
    --divider: #e45a47;
  }
  * { box-sizing: border-box; margin: 0; padding: 0; }
  html, body { width: 1200px; height: 900px; overflow: hidden; }
  body {
    background: var(--backdrop);
    font-family: "Cabin", sans-serif;
    position: relative;
  }
  .card {
    position: absolute;
    left: 250px;
    width: 700px;
    height: 400px;
    border-radius: 36px;
    overflow: hidden;
  }
  /* Reverse side */
  .card-back {
    top: 30px;
    background: linear-gradient(100deg, var(--coral) 0%, var(--coral-light) 100%);
  }
  .back-brand {
    position: absolute;
    left: 0; right: 0;
    top: 135px;
    text-align: center;
    color: #ffffff;
    font-weight: 700;
    font-size: 52px;
    letter-spacing: 1px;
  }
  .back-rule {
    position: absolute;
    left: 175px;
    width: 350px;
    top: 222px;
    height: 1px;
    background: linear-gradient(90deg, rgba(255,255,255,0), rgba(255,255,255,0.8), rgba(255,255,255,0));
  }
  .back-tagline {
    position: absolute;
    left: 0; right: 0;
    top: 236px;
    text-align: center;
    color: #ffffff;
    font-family: "Alegreya Sans", sans-serif;
    font-weight: 500;
    font-size: 22px;
    letter-spacing: 4px;
  }
  /* Front side */
  .card-front {
    top: 470px;
    background: linear-gradient(110deg, #f7f7f7 0%, #e9e9e9 55%, #fafafa 100%);
  }
  .front-brand {
    position: absolute;
    left: 60px;
    top: 150px;
    color: var(--brand-blue);
    font-weight: 700;
    font-size: 58px;
    letter-spacing: 0.5px;
  }
  .holder {
    position: absolute;
    right: 330px;
    top: 265px;
    text-align: right;
    line-height: 1.3;
  }
  .holder-name {
    color: var(--brand-blue);
    font-weight: 600;
    font-size: 17px;
    letter-spacing: 0.5px;
    text-transform: uppercase;
  }
  .holder-role, .holder-company {
    color: var(--ink);
    font-size: 15px;
  }
  .divider {
    position: absolute;
    left: 385px;
    top: 235px;
    width: 1px;
    height: 110px;
    background: var(--divider);
  }
  .contacts {
    position: absolute;
    left: 400px;
    top: 232px;
    list-style: none;
    color: var(--ink);
    font-size: 14px;
    line-height: 1.6;
  }
  .contacts li { display: flex; align-items: flex-start; gap: 8px; }
  .contacts svg { width: 14px; height: 14px; margin-top: 4px; flex-shrink: 0; }
  .contacts .indent { padding-left: 22px; }
</style>
</head>
<body>
  <section class="card card-back" aria-label="Card reverse">
    <div class="back-brand">Vexalund</div>
    <div class="back-rule"></div>
    <div class="back-tagline">Cures Across Borders</div>
  </section>

  <section class="card card-front" aria-label="Card front">
    <div class="front-brand">Vexalund</div>

    <div class="holder">
      <div class="holder-name">Ravin K. Solanki</div>
      <div class="holder-role">CEO</div>
      <div class="holder-company">Vexalund</div>
    </div>

    <div class="divider"></div>

    <ul class="contacts">
      <li>
        <svg viewBox="0 0 14 14" aria-hidden="true"><rect x="3.5" y="1" width="7" height="12" rx="1.5" fill="none" stroke="#2391c9" stroke-width="1.4"/><circle cx="7" cy="11" r="0.8" fill="#2391c9"/></svg>
        <span>+919812345670</span>
      </li>
      <li>
        <svg viewBox="0 0 14 14" aria-hidden="true"><rect x="1" y="3" width="12" height="8.5" fill="#2391c9"/><path d="M1 3 L7 8 L13 3" fill="none" stroke="#ffffff" stroke-width="1.2"/></svg>
        <span>rsolanki@vexalund.com</span>
      </li>
      <li>
        <svg viewBox="0 0 14 14" aria-hidden="true"><g fill="none" stroke="#2391c9" stroke-width="1.1"><circle cx="7" cy="7" r="5.8"/><ellipse cx="7" cy="7" rx="2.6" ry="5.8"/><line x1="1.2" y1="7" x2="12.8" y2="7"/></g></svg>
        <span>www.vexalund.com</span>
      </li>
      <li>
        <svg viewBox="0 0 14 14" aria-hidden="true"><path d="M7 13 C7 13 2.5 8 2.5 5.2 A4.5 4.5 0 0 1 11.5 5.2 C11.5 8 7 13 7 13 Z" fill="#2391c9"/><circle cx="7" cy="5.2" r="1.6" fill="#ffffff"/></svg>
        <span>14, Lotus Park Colony</span>
      </li>
      <li class="indent"><span>Nashik Road, 422101, India</span></li>
    </ul>
  </section>
</body>
</html>
```